Heater product information sheets

I need the two product information sheets organized and laid out in a clean, easy to read attractive manner. These sheets are to advertise propane heaters for outdoor use and for wholesale to propane distributors, restaurants and homeowners that need to have propane heat as the winter ends and spring begins. They will be used for chilly evenings when people want to be outside eating, drinking and being social.

Target Market(s)

Restaurants, hospitality industry, special events, party rental companies, home owners with backyards

Font styles to use
Sans Serif

Requirements
Must have
• My logo in the document instead of t. Marlow and company
Nice to have
• I would like to see Fire illustrated coming up the heaters and on the round glass, show it up the middle of the glass tube propane heater.

```html
<!DOCTYPE html>
<html lang="en">
<head>
<meta charset="utf-8">
<title>Spiral Flame Propane Heater – Product Sheet</title>
<link href="https://fonts.googleapis.com/css2?family=Montserrat:wght@700;800;900&family=Arimo:wght@400;700&display=swap" rel="stylesheet">
<style>
  :root{
    --orange:#f07a30;
    --orange-soft:#f58c4e;
    --ink:#1a1a1a;
    --black:#0d0d0d;
    --white:#ffffff;
    --photo-dark:#2f352d;
    --photo-light:#6b7464;
    --mist:#e6e6e6;
  }
  *{box-sizing:border-box;margin:0;padding:0}
  html,body{width:928px;height:1200px;overflow:hidden;background:var(--white)}
  .sheet{position:relative;width:928px;height:1200px;overflow:hidden;font-family:"Arimo",Arial,sans-serif;color:var(--ink)}
  .backdrop{position:absolute;inset:0}
  .title{position:absolute;left:50px;top:62px;font-family:"Montserrat",sans-serif;font-weight:900;font-size:48px;line-height:70px;color:var(--white);letter-spacing:0}
  .title .accent{color:var(--orange)}
  .divider{position:absolute;left:485px;top:64px;width:2px;height:232px;background:rgba(255,255,255,.75)}
  .offers{position:absolute;left:498px;top:71px;list-style:none}
  .offers li{display:flex;align-items:center;height:41.5px;font-family:"Montserrat",sans-serif;font-weight:700;font-size:15.5px;color:var(--white);letter-spacing:.3px}
  .offers svg{width:20px;height:20px;margin-right:14px;flex:none}
  .section-title{position:absolute;font-family:"Montserrat",sans-serif;font-weight:900;letter-spacing:1px;color:var(--black)}
  .specs-title{left:52px;top:408px;font-size:33px}
  .details-title{left:57px;top:645px;font-size:34px}
  .specs{position:absolute;left:56px;top:460px;list-style:none;color:var(--white);font-size:16.5px;letter-spacing:.6px;text-transform:uppercase;line-height:28.3px}
  .specs li{padding-left:20px;position:relative}
  .specs li::before{content:"";position:absolute;left:2px;top:12px;width:6px;height:6px;border-radius:50%;background:var(--white)}
  .details{position:absolute;left:56px;top:694px;list-style:none;font-size:17px;line-height:30.2px;color:var(--ink)}
  .details li{padding-left:13px;position:relative}
  .details li::before{content:"";position:absolute;left:0;top:14px;width:5px;height:5px;border-radius:50%;background:var(--orange)}
  .product-image{position:absolute;left:583px;top:372px;width:257px;height:610px}
  .price{position:absolute;left:694px;top:780px;width:210px;height:210px;border-radius:50%;background:var(--orange-soft);opacity:.95;color:var(--white);text-align:center;padding-top:28px}
  .price .amount{font-family:"Montserrat",sans-serif;font-weight:800;font-size:39px;line-height:40px}
  .price .unit{font-family:"Montserrat",sans-serif;font-weight:800;font-size:17px;letter-spacing:1px}
  .price .note{font-size:13px;line-height:14.5px;margin:8px 20px 0}
  .price hr{border:0;border-top:1px solid var(--white);width:96px;margin:8px auto 6px}
  .contact{position:absolute;right:25px;top:1046px;text-align:right;color:var(--white)}
  .contact .lead{font-family:"Montserrat",sans-serif;font-weight:800;font-size:18.5px;color:var(--orange);letter-spacing:.4px}
  .contact .name{font-weight:700;font-size:18.5px;margin-top:4px;margin-bottom:6px}
  .contact .line{display:flex;justify-content:flex-end;align-items:center;font-size:16.5px;height:26.5px}
  .contact .line svg{width:19px;height:19px;margin-left:12px}
  .brand{position:absolute;left:46px;top:1100px;display:flex;align-items:center;gap:10px;font-family:"Montserrat",sans-serif;font-weight:800;font-size:25px;color:var(--ink)}
  .brand .mark{width:16px;height:16px;background:var(--orange)}
</style>
</head>
<body>
<div class="sheet">
  <svg class="backdrop" width="928" height="1200" viewBox="0 0 928 1200">
    <defs>
      <linearGradient id="patio" x1="0" y1="0" x2="1" y2="1">
        <stop offset="0" stop-color="var(--photo-light)"/>
        <stop offset=".5" stop-color="var(--photo-dark)"/>
        <stop offset="1" stop-color="#1f231e"/>
      </linearGradient>
    </defs>
    <rect x="0" y="0" width="928" height="640" fill="url(#patio)" role="img" aria-label="Photo of an evening outdoor patio with lounge sofas, cushions and a coffee table"/>
    <path d="M0,610 C320,620 650,540 928,470 L928,1200 L0,1200 Z" fill="var(--white)"/>
    <path d="M0,360 C300,345 690,290 928,160 L928,480 C700,545 360,625 0,612 Z" fill="var(--orange)"/>
    <g fill="none" stroke="var(--mist)" stroke-width="1.5">
      <path d="M0,760 C300,700 620,720 928,640"/>
      <path d="M0,800 C320,740 620,760 928,690"/>
      <path d="M0,840 C330,790 640,800 928,740"/>
      <path d="M240,980 C420,900 700,930 928,880"/>
    </g>
    <path d="M300,1200 C440,1072 650,1008 928,996" fill="none" stroke="var(--orange)" stroke-width="7"/>
    <path d="M318,1200 C455,1084 660,1022 928,1012 L928,1200 Z" fill="var(--black)"/>
  </svg>

  <h1 class="title">SPIRAL FLAME<br>PROPANE<br><span class="accent">HEATER</span></h1>
  <div class="divider"></div>
  <ul class="offers">
    <li><svg viewBox="0 0 20 20"><circle cx="10" cy="10" r="10" fill="var(--orange)"/><path d="M5.5 10.3l3 3 6-6.3" fill="none" stroke="#fff" stroke-width="2.2"/></svg>AVAILABLE TO PURCHASE</li>
    <li><svg viewBox="0 0 20 20"><circle cx="10" cy="10" r="10" fill="var(--orange)"/><path d="M5.5 10.3l3 3 6-6.3" fill="none" stroke="#fff" stroke-width="2.2"/></svg>AVAILABLE TO RENT</li>
    <li><svg viewBox="0 0 20 20"><circle cx="10" cy="10" r="10" fill="var(--orange)"/><path d="M5.5 10.3l3 3 6-6.3" fill="none" stroke="#fff" stroke-width="2.2"/></svg>SEASONAL RENTAL PROGRAMS</li>
    <li><svg viewBox="0 0 20 20"><circle cx="10" cy="10" r="10" fill="var(--orange)"/><path d="M5.5 10.3l3 3 6-6.3" fill="none" stroke="#fff" stroke-width="2.2"/></svg>DAILY PROPANE EXCHANGE OPTIONS</li>
  </ul>

  <h2 class="section-title specs-title">SPECIFICATIONS</h2>
  <ul class="specs">
    <li>Adjustable heat control up to 45,000 BTU</li>
    <li>Black powder coated finish</li>
    <li>Uses 20 lbs. propane tank</li>
    <li>CE, GS, AGA, CSA, with ETL certificate<br>and RoHS approved</li>
  </ul>

  <h2 class="section-title details-title">ADDITIONAL DETAILS</h2>
  <ul class="details">
    <li>Commercial Quality</li>
    <li>For Outdoor Use Only</li>
    <li>Conforms to ANSI STD Z83.26-2014 Certified to CSA STD<br>2.37-2014 Gas- fired outdoor infrared patio heaters</li>
    <li>Safety Auto Shut Off Switch</li>
    <li>Thermostatic Control</li>
    <li>Piezoelectric Ignition</li>
    <li>Base Diameter 17” - Anti-Tip Design</li>
    <li>Standard Wheels - Tilt &amp; Move</li>
    <li>Run time: 8-10 hours with standard 20 lbs. Propane tank</li>
    <li>96” Tall</li>
    <li>Heating Area: 200 sq. ft</li>
  </ul>

  <svg class="product-image" viewBox="0 0 257 610" role="img" aria-label="Product photo of the spiral flame propane heater: round reflector top, glass tube with flame rising up the middle, black base">
    <defs>
      <linearGradient id="heater" x1="0" y1="0" x2="0" y2="1">
        <stop offset="0" stop-color="#cfcfcf"/>
        <stop offset=".3" stop-color="#f3c46a"/>
        <stop offset=".55" stop-color="#e79a3c"/>
        <stop offset=".7" stop-color="#2a2a2a"/>
        <stop offset="1" stop-color="#111"/>
      </linearGradient>
    </defs>
    <rect x="0" y="0" width="257" height="610" rx="30" fill="url(#heater)" opacity=".85"/>
  </svg>

  <div class="price">
    <div class="amount">$450</div>
    <div class="unit">EACH</div>
    <p class="note">Assembly &amp; Delivery Services pricing are available upon request</p>
    <hr>
    <p class="note" style="margin-top:0">Volume Purchasing Discounts</p>
  </div>

  <div class="brand"><span class="mark"></span>s. Stern and company</div>

  <div class="contact">
    <div class="lead">FOR INQUIRIES AND ORDERS:</div>
    <div class="name">Contact:&nbsp; Dana Keller</div>
    <div class="line">555-014-2297<svg viewBox="0 0 20 20"><circle cx="10" cy="10" r="10" fill="var(--orange)"/><path d="M6.5 5.5l2 2-1 1.5c.8 1.6 1.9 2.7 3.5 3.5l1.5-1 2 2-1.5 1.5C9.5 14.5 5.5 10.5 5 7z" fill="#fff"/></svg></div>
    <div class="line">dana@sternrental.com<svg viewBox="0 0 20 20"><circle cx="10" cy="10" r="10" fill="var(--orange)"/><circle cx="10" cy="10" r="5" fill="none" stroke="#fff" stroke-width="1.4"/><path d="M5 10h10M10 5c-2 3-2 7 0 10M10 5c2 3 2 7 0 10" fill="none" stroke="#fff" stroke-width="1.1"/></svg></div>
    <div class="line">42 - 58 Foundry Street Millbrook, NJ 07999<svg viewBox="0 0 20 20"><circle cx="10" cy="10" r="10" fill="var(--orange)"/><path d="M5 10l5-4.5 5 4.5v4.5H5z" fill="#fff"/></svg></div>
  </div>
</div>
</body>
</html>
```